Brell Stone Company Business Cards

Front and Back Business Card - logo and text setup - cool design. I need workable photoshop or illustrator files so I can setup each employee card with design that is created
Updates

Hi everyone, thank you for the great entries. Please no more white and blue cards - there are so many already - black and silver only now please. thanks!

Target Market(s)

Construction Industry - Facility Managers

Industry/Entity Type

Construction

Contact Information for Business Card

I really like contemporary simplistic looks - clean neat....not opposed to seeing some black backrounds

Requirements
Must have
• Logo/website address with design on front only - www.brellstone-example.com (logo attached)
• Back:
• Name/Title/Company Address/Phone/email address
Nice to have
• Cool design
Should not have
• Nothing gimmicky like Fire or Water - since we are a Fire Protection company - it has all been done

```html
<!DOCTYPE html>
<html lang="en">
<head>
<meta charset="utf-8">
<title>Brell Stone Company – Business Cards</title>
<link href="https://fonts.googleapis.com/css2?family=Source+Sans+3:ital,wght@0,400;0,700;0,900;1,400;1,700&display=swap" rel="stylesheet">
<style>
  :root {
    --stage: #c9ccce;
    --card: #000000;
    --band: #0324a0;
    --brand: #ff2222;
    --ink: #ffffff;
    --rule: #5a6fc4;
  }
  * { margin: 0; padding: 0; box-sizing: border-box; }
  html, body { width: 1200px; height: 1193px; overflow: hidden; }
  body {
    background: var(--stage);
    position: relative;
    font-family: "Source Sans 3", sans-serif;
    color: var(--ink);
  }
  .card {
    position: absolute;
    width: 871px;
    height: 498px;
    background: var(--card);
    border-radius: 21px;
    overflow: hidden;
  }
  .card--contact { left: 258px; top: 81px; }
  .card--brand { left: 63px; top: 623px; }

  .wordmark {
    position: absolute;
    left: 0; right: 0;
    text-align: center;
    font-weight: 900;
    color: var(--brand);
    letter-spacing: -0.01em;
    line-height: 1;
    white-space: nowrap;
  }
  .card--contact .wordmark { top: 88px; font-size: 84px; }
  .card--brand .wordmark { top: 160px; font-size: 108px; }

  .holder {
    position: absolute;
    top: 236px; left: 0; right: 0;
    text-align: center;
    font-size: 30px;
    font-style: italic;
    line-height: 1;
  }
  .holder__name { font-weight: 700; }
  .holder__title { font-weight: 400; }

  .band {
    position: absolute;
    left: 0; right: 0;
    background: var(--band);
  }
  .card--contact .band { top: 291px; height: 161px; }
  .card--brand .band { top: 400px; height: 53px; }

  .address {
    position: absolute;
    right: 458px; top: 25px;
    text-align: right;
    font-style: normal;
    font-size: 23px;
    line-height: 38.5px;
  }
  .divider {
    position: absolute;
    left: 435px; top: 30px;
    width: 1px; height: 100px;
    background: var(--rule);
  }
  .contacts {
    position: absolute;
    left: 459px; top: 25px;
    list-style: none;
    font-size: 23px;
    line-height: 38.5px;
  }
  .contacts li { display: flex; align-items: center; gap: 10px; }
  .contacts svg { width: 22px; height: 22px; flex: none; }

  .website {
    position: absolute;
    left: 0; right: 0; top: 0;
    height: 53px;
    line-height: 53px;
    text-align: center;
    font-size: 25px;
    letter-spacing: 0.22em;
  }
</style>
</head>
<body>

  <section class="card card--contact" aria-label="Business card, contact side">
    <div class="wordmark">Brell Stone</div>
    <p class="holder"><span class="holder__name">Mara Keller,</span> <span class="holder__title">President</span></p>
    <div class="band">
      <address class="address">48 Harbor Park Lane<br>Millbrook<br>NY 10950</address>
      <span class="divider"></span>
      <ul class="contacts">
        <li>
          <svg viewBox="0 0 24 24" aria-hidden="true"><path fill="#fff" d="M6.6 2.5l3 3.2-1.8 2.4c1.2 2.7 3.4 4.9 6.1 6.1l2.4-1.8 3.2 3-1.9 3.6C10.5 18.6 5.4 13.5 3 6.4z"/></svg>
          (555) 014-2290
        </li>
        <li>
          <svg viewBox="0 0 24 24" aria-hidden="true"><rect x="2" y="5" width="20" height="14" fill="#fff"/><path d="M2.5 5.5l9.5 8 9.5-8M2.5 18.5l7-6.5M21.5 18.5l-7-6.5" fill="none" stroke="#0324a0" stroke-width="1.6"/></svg>
          info@brellstone-example.com
        </li>
        <li>
          <svg viewBox="0 0 24 24" aria-hidden="true"><g fill="none" stroke="#fff" stroke-width="1.5"><circle cx="12" cy="12" r="10"/><ellipse cx="12" cy="12" rx="4.5" ry="10"/><path d="M2 12h20M4 6.5h16M4 17.5h16M12 2v20"/></g></svg>
          www.brellstone-example.com
        </li>
      </ul>
    </div>
  </section>

  <section class="card card--brand" aria-label="Business card, brand side">
    <div class="wordmark">Brell Stone</div>
    <div class="band">
      <p class="website">www.brellstone-example.com</p>
    </div>
  </section>

</body>
</html>
```